Eyecatching website design for commercial lighting business

This contest is all about the graphic design aspect. We need a striking website design for a commercial lighting company. We want something really eye catching to introduce people to our range of induction and LED lights which save businesses money on maintenance and electricity costs.

To be successful in this contest you will need to provide a design and pictures for the pages listed below.

We are using the platform velbrin.com.au and you can see the attached template which everything will be loaded into so we just need HTML files which we can upload and we can do everything else from Velbrin.

The final design should be strong and clean and use the colours and textures in the attached business card file.

Detailed requirements:

Please see attached screenshot of the website template, all we need is a fantastic graphic design and improvement/ incorporation of our logo for the following pages
Page Headings:
1. Home
About Us, Contact Us, snapshot of and link to Blog

Each of the below pages will have several paragraphs of text followed by a list of suitable products which is generated from our product catalogue.

2. Car Park Lighting
3. Educational Lighting
4. Hospitality Lighting
5. Office & Shop Lighting
6. Warehouse Lighting

Some of the website we have seen which are similar in nature are:
http://www.quorvanlamps.com.au/
http://www.tibrox.com/
http://www.gandowlumen.net/commercial-led
but we really want a modern, eye catching and memorable design

Some of the designs built on Velbrin that we like are:

http://www.pemberhollow.com.au/
http://www.marwickgoods.com.au/
http://www.kelmorabay.com.au/

I've also uploaded a couple of photos that we love. We'd like something similar for each industry.

Target Market(s)

Company Owners, Maintenance & Facilities Managers, Electrical Contractors

Industry/Entity Type

Electrical

Coding

Coded - Design and coding required

Number of Pages Required

5+ page

Font styles to use
Sans Serif

Colors
33a6d7
ec1f27

Requirements
Must have
• -Must scale to mobile
• -HTML coded files need to be provided (HTML Bootstrap)
Nice to have
• -Prefer incorporation of our logo into header bar
• -Design of 2-3 advertising banners which can be displayed on the home page
• -Prominent call to action button towards top of page 'Get a quote' or similar
• -Grid based design HTML Bootstrap

```html
<!DOCTYPE html>
<html lang="en">
<head>
<meta charset="utf-8">
<title>K&amp;R Holt Business Solutions — Commercial Lighting</title>
<link href="https://fonts.googleapis.com/css2?family=Open+Sans:wght@400;600;700&family=Oswald:wght@400;500;700&display=swap" rel="stylesheet">
<style>
:root{
  --blue:#33a6d7;
  --red:#ec1f27;
  --ink:#2a2a2a;
  --text:#6b6b6b;
  --light:#f1f2f4;
  --line:#e2e4e7;
  --footer:#1f2022;
  --footer-bottom:#151617;
  --white:#ffffff;
}
*{box-sizing:border-box;margin:0;padding:0}
html,body{width:1200px;height:2784px;overflow:hidden}
body{font-family:"Open Sans",Arial,sans-serif;color:var(--text);background:var(--white);font-size:14px;line-height:1.6}
h1,h2,h3,h4{font-family:"Oswald","Arial Narrow",sans-serif;color:var(--ink);font-weight:500;text-transform:uppercase}
.btn{display:inline-block;font-family:"Oswald",sans-serif;font-size:14px;letter-spacing:1px;color:var(--white);padding:10px 26px;border-radius:3px;text-transform:uppercase}
.btn-red{background:var(--red)}
.btn-blue{background:var(--blue)}
.ph{display:block}

/* header */
.site-header{height:56px;position:relative;background:var(--white);border-bottom:1px solid var(--line)}
.brand{position:absolute;left:28px;top:8px;height:40px;display:flex;align-items:center;gap:10px;background:#141414;padding:0 16px}
.brand-mark{width:14px;height:14px;background:var(--red)}
.brand-name{font-family:"Oswald",sans-serif;font-size:17px;font-weight:500;color:var(--white);letter-spacing:1px;text-transform:uppercase}
.main-nav{position:absolute;right:0;top:0;height:44px;width:600px;background:var(--red);display:flex;justify-content:flex-end;align-items:center;padding-right:40px;gap:34px}
.main-nav a{font-family:"Oswald",sans-serif;font-size:14px;color:var(--white);letter-spacing:1px;text-transform:uppercase;text-decoration:none}

/* hero */
.hero{height:544px;position:relative;background:linear-gradient(180deg,#fafbfc,#e6e8eb)}
.hero-copy{position:absolute;left:100px;top:150px;width:430px}
.hero-copy h1{font-size:66px;font-weight:700;color:var(--blue);line-height:1}
.hero-copy h2{font-size:26px;font-weight:500;margin-top:8px;letter-spacing:.5px}
.hero-copy p{margin-top:14px;font-size:14px}
.hero-copy .btn{margin-top:26px;padding:12px 28px}
.hero-media{position:absolute;right:100px;top:40px;width:560px;height:440px;border-radius:50% 44% 48% 50%;background:radial-gradient(circle at 55% 50%,#f4f5f6 0,#b9bdc2 40%,#3d4045 70%,#e6e8eb 71%)}
.hero-dots{position:absolute;left:0;right:0;bottom:22px;display:flex;justify-content:center;gap:12px}
.hero-dots span{width:12px;height:12px;border-radius:50%;background:#c4c7cb}
.hero-dots span.on{background:var(--blue)}

/* welcome */
.welcome{height:340px;text-align:center;padding:70px 150px 0}
.welcome h2{font-size:26px;line-height:1.3}
.welcome p{margin:20px auto 0;width:880px;font-size:13px}
.welcome .btn{margin-top:28px}

/* sectors */
.sectors{height:440px;background:var(--light);position:relative;border-top:1px solid var(--line);border-bottom:1px solid var(--line)}
.sector-row{position:absolute;left:100px;right:100px;top:50px;display:flex;gap:40px}
.sector-card{flex:1}
.sector-card .ph{height:200px;border-radius:2px}
.sector-card h3{margin-top:18px;font-size:18px;color:var(--blue)}
.sector-card p{font-size:13px;margin-top:6px}
.sector-card .more{display:block;margin-top:8px;font-size:13px;color:var(--red);font-weight:600}
.slider-arrow{position:absolute;top:170px;width:40px;height:40px;border-radius:50%;background:var(--white);border:1px solid var(--line)}
.slider-arrow.prev{left:24px}
.slider-arrow.next{right:24px}
.slider-arrow svg{display:block;margin:12px auto}

/* video */
.video-block{height:360px;position:relative}
.video-frame{position:absolute;left:100px;top:40px;width:480px;height:290px;background:linear-gradient(135deg,#2b1a0f,#7a4a1e 55%,#1c130c)}
.video-frame .play{position:absolute;left:210px;top:110px}
.video-bar{position:absolute;left:0;right:0;bottom:0;height:28px;background:rgba(0,0,0,.6)}
.video-bar i{position:absolute;left:40px;top:13px;width:380px;height:3px;background:#666}
.video-bar b{position:absolute;left:40px;top:13px;width:120px;height:3px;background:var(--blue)}
.video-copy{position:absolute;left:640px;top:46px;width:460px}
.video-copy h2{font-size:26px}
.video-copy h4{font-family:"Open Sans",sans-serif;text-transform:none;color:var(--blue);font-size:14px;font-weight:700;margin-top:6px}
.video-copy p{font-size:13px;margin-top:12px}
.video-copy .btn{margin-top:20px}

/* blog */
.blog{height:540px;position:relative}
.blog-head{position:absolute;left:100px;right:100px;top:30px;display:flex;justify-content:space-between;align-items:center;border-bottom:1px solid var(--line);padding-bottom:12px}
.blog-head h2{font-size:26px}
.blog-nav{display:flex;gap:4px}
.blog-nav span{width:28px;height:28px;background:#d9dbde;display:flex;align-items:center;justify-content:center}
.post{position:absolute;left:150px;top:110px;width:900px;height:350px;background:var(--light)}
.post-body{position:absolute;left:40px;top:40px;width:420px}
.post-body h3{font-size:20px}
.post-meta{display:flex;gap:18px;font-size:12px;color:#999;margin-top:8px}
.post-meta span::before{content:"";display:inline-block;width:8px;height:8px;background:var(--blue);margin-right:6px}
.post-body p{font-size:13px;margin-top:12px}
.post-body .btn{margin-top:20px}
.post .ph{position:absolute;right:-30px;top:40px;width:420px;height:270px;background:linear-gradient(135deg,#5a1410,#b8321c 45%,#2a0c08)}

/* footer */
.site-footer{height:420px;background:var(--footer);position:relative;color:#a7a9ac}
.footer-cols{position:absolute;left:100px;right:100px;top:46px;display:flex;gap:60px}
.footer-col{flex:1}
.footer-col h4{font-size:17px;color:var(--white);margin-bottom:18px}
.footer-col h4 em{font-style:normal;color:var(--blue)}
.footer-col p,.footer-col li{font-size:13px}
.recent p{color:#d0d2d4}
.recent small{display:block;color:var(--blue);font-size:12px;margin-bottom:16px}
.ticks{list-style:none}
.ticks li{display:flex;align-items:center;gap:10px;margin-bottom:8px}
.contact p{margin-bottom:6px}
.contact strong{color:var(--white);font-weight:600}
.subscribe{display:flex;margin-top:14px}
.subscribe span{flex:1;height:36px;background:var(--white);color:#999;font-size:12px;padding:9px 12px}
.subscribe b{background:var(--blue);color:var(--white);font-family:"Oswald",sans-serif;font-weight:400;font-size:13px;padding:9px 16px}
.contact small{display:block;font-size:12px;margin-top:10px}
.footer-bottom{position:absolute;left:0;right:0;bottom:0;height:44px;background:var(--footer-bottom);text-align:center;font-size:12px;line-height:44px;color:#77797c}
</style>
</head>
<body>

<header class="site-header">
  <div class="brand"><span class="brand-mark"></span><span class="brand-name">K&amp;R Holt Business Solutions</span></div>
  <nav class="main-nav">
    <a href="#">Home</a><a href="#">About Us</a><a href="#">Products</a><a href="#">Blog</a><a href="#">Contact Us</a>
  </nav>
</header>

<section class="hero">
  <div class="hero-copy">
    <h1>LED Lights</h1>
    <h2>Save businesses money on maintenance</h2>
    <p>Bright, efficient fittings that cut power bills and trim upkeep for every site you manage, from car parks to busy office floors.</p>
    <a class="btn btn-red" href="#">Get More</a>
  </div>
  <div class="hero-media ph" role="img" aria-label="Close-up photo of LED spot lamps"></div>
  <div class="hero-dots"><span></span><span class="on"></span><span></span><span></span></div>
</section>

<section class="welcome">
  <h2>Welcome to the commercial lighting division of<br>K&amp;R Holt Business Solutions</h2>
  <p>Our lighting division helps business owners and facility managers replace tired fittings with induction and LED lights that last longer, use less power and need far less upkeep. We survey each site, plan the layout and supply a full range of fittings to suit car parks, schools, hotels, offices, shops and warehouses.</p>
  <a class="btn btn-blue" href="#">Read More</a>
</section>

<section class="sectors">
  <span class="slider-arrow prev"><svg width="10" height="16" viewBox="0 0 10 16"><path d="M8 2 2 8l6 6" fill="none" stroke="#999" stroke-width="2"/></svg></span>
  <div class="sector-row">
    <article class="sector-card">
      <div class="ph" role="img" aria-label="Photo of a brightly lit underground car park" style="background:linear-gradient(135deg,#6f6a5c,#c9b98f 50%,#4c4a44)"></div>
      <h3>Car Park Lighting</h3>
      <p>Durable fittings that keep parking levels bright and safe while using less power every single night.</p>
      <span class="more">Read more</span>
    </article>
    <article class="sector-card">
      <div class="ph" role="img" aria-label="Photo of a warmly lit restaurant interior" style="background:linear-gradient(135deg,#3a1f0c,#c98a3a 50%,#2a160a)"></div>
      <h3>Hospitality Lighting</h3>
      <p>Warm, welcoming light for hotels, bars and restaurants that keeps running costs low all year round.</p>
      <span class="more">Read more</span>
    </article>
    <article class="sector-card">
      <div class="ph" role="img" aria-label="Photo of a modern open-plan office" style="background:linear-gradient(135deg,#b7c3cc,#eef2f5 50%,#8e9aa3)"></div>
      <h3>Office Lighting</h3>
      <p>Even, glare-free light for desks and meeting rooms that helps staff focus and trims the power bill.</p>
      <span class="more">Read more</span>
    </article>
  </div>
  <span class="slider-arrow next"><svg width="10" height="16" viewBox="0 0 10 16"><path d="m2 2 6 6-6 6" fill="none" stroke="#999" stroke-width="2"/></svg></span>
</section>

<section class="video-block">
  <div class="video-frame ph" role="img" aria-label="Video still of glowing filament lamps">
    <svg class="play" width="60" height="60" viewBox="0 0 60 60"><rect width="60" height="60" rx="8" fill="#fff" fill-opacity=".9"/><path d="M23 18v24l20-12z" fill="#222"/></svg>
    <div class="video-bar"><i></i><b></b></div>
  </div>
  <div class="video-copy">
    <h2>LED lights which save businesses</h2>
    <h4>Commercial lighting company</h4>
    <p>Induction and LED fittings give steady, even light and run for years without a lamp change, which keeps ladders and call-outs to a minimum.</p>
    <p>Our team works with owners, facility managers and electrical contractors to choose the right fittings, plan the upgrade and track the savings.</p>
    <a class="btn btn-blue" href="#">Read More</a>
  </div>
</section>

<section class="blog">
  <div class="blog-head">
    <h2>Our Blog</h2>
    <div class="blog-nav">
      <span><svg width="8" height="12" viewBox="0 0 8 12"><path d="M6 1 1 6l5 5" fill="none" stroke="#fff" stroke-width="2"/></svg></span>
      <span><svg width="8" height="12" viewBox="0 0 8 12"><path d="m2 1 5 5-5 5" fill="none" stroke="#fff" stroke-width="2"/></svg></span>
    </div>
  </div>
  <article class="post">
    <div class="post-body">
      <h3>Perspiciatis unde omnis iste natus error</h3>
      <div class="post-meta"><span>12 Jan 2015</span><span>By Admin</span><span>Tags</span></div>
      <p>Switching a building to LED is one of the quickest ways to cut running costs without changing how the space is used.</p>
      <p>This post looks at payback times, light levels and the small details that make an upgrade run smoothly from start to finish.</p>
      <a class="btn btn-blue" href="#">Read More</a>
    </div>
    <div class="ph" role="img" aria-label="Photo of a hotel lobby lit in warm red tones"></div>
  </article>
</section>

<footer class="site-footer">
  <div class="footer-cols">
    <div class="footer-col recent">
      <h4>Recent <em>Posts</em></h4>
      <p>How LED upgrades cut warehouse power costs</p>
      <small>12 Jan 2015</small>
      <p>Choosing the right lighting for school halls</p>
      <small>28 Dec 2014</small>
    </div>
    <div class="footer-col">
      <h4>Induction and <em>LED Lights</em></h4>
      <ul class="ticks">
        <li><svg width="12" height="12" viewBox="0 0 12 12"><path d="m1 6 3 3 7-7" fill="none" stroke="#33a6d7" stroke-width="2"/></svg>Induction lamps last up to 100,000 hours</li>
        <li><svg width="12" height="12" viewBox="0 0 12 12"><path d="m1 6 3 3 7-7" fill="none" stroke="#33a6d7" stroke-width="2"/></svg>LED fittings use far less power</li>
        <li><svg width="12" height="12" viewBox="0 0 12 12"><path d="m1 6 3 3 7-7" fill="none" stroke="#33a6d7" stroke-width="2"/></svg>Fewer lamp changes and call-outs</li>
        <li><svg width="12" height="12" viewBox="0 0 12 12"><path d="m1 6 3 3 7-7" fill="none" stroke="#33a6d7" stroke-width="2"/></svg>Instant start with no flicker</li>
        <li><svg width="12" height="12" viewBox="0 0 12 12"><path d="m1 6 3 3 7-7" fill="none" stroke="#33a6d7" stroke-width="2"/></svg>Even light across large areas</li>
        <li><svg width="12" height="12" viewBox="0 0 12 12"><path d="m1 6 3 3 7-7" fill="none" stroke="#33a6d7" stroke-width="2"/></svg>Site surveys and upgrade plans</li>
      </ul>
    </div>
    <div class="footer-col contact">
      <h4>Contact <em>Info</em></h4>
      <p>14 Ferren Lane, Suite 3,<br>Dunmore QLD 4352</p>
      <p><strong>P:</strong> (07) 5550 1234 &nbsp; <strong>F:</strong> (07) 5550 1299</p>
      <p>sales@krholt.com.au</p>
      <div class="subscribe"><span>Enter Email</span><b>Submit</b></div>
      <small>Join our list for product news and offers.</small>
    </div>
  </div>
  <div class="footer-bottom">Copyright © 2015 K&amp;R Holt Business Solutions. All rights reserved.</div>
</footer>

</body>
</html>
```